Business Card Design

Business Card for professional consulting firm working with large financial institutions.

Target Market(s)

Executive buyers

Industry/Entity Type

Banking

Contact Information for Business Card

Mild creativity wanted. Not boring, but do elaborate artwork.

Font styles to use
Serif
Sans Serif

Colors

Designer to choose colors to be used in the design.

Requirements
Must have
• Standard business card features - company name, individual name, telephone, website, email, locations.
Nice to have
• Two colors
Should not have
• too many colors, fancy printing, cartoons.

```html
<!DOCTYPE html>
<html lang="en">
<head>
<meta charset="utf-8">
<title>Harlow Advisory business card</title>
<link rel="stylesheet" href="https://fonts.googleapis.com/css2?family=Work+Sans:wght@400;500&display=swap">
<style>
  :root {
    --backdrop: #262626;
    --card: #1a1a1a;
    --card-edge: #222;
    --ink: #f2f2f2;
    --ink-soft: #d6d6d6;
    --ink-muted: #bdbdbd;
  }
  html, body {
    margin: 0;
    width: 1200px;
    height: 900px;
    overflow: hidden;
    background: var(--backdrop);
  }
  .sheet {
    position: relative;
    width: 1200px;
    height: 900px;
  }
  .card {
    position: absolute;
    left: 250px;
    width: 700px;
    height: 400px;
    background: linear-gradient(135deg, var(--card) 0%, var(--card-edge) 100%);
    box-shadow: 0 12px 30px rgba(0,0,0,0.55);
  }
  .card--front { top: 35px; }
  .card--back { top: 465px; }

  .wordmark {
    font-family: "Work Sans", sans-serif;
    font-weight: 500;
    color: var(--ink);
    display: flex;
    align-items: center;
    gap: 14px;
    white-space: nowrap;
  }
  .wordmark__dot {
    width: 14px;
    height: 14px;
    border-radius: 50%;
    background: var(--ink);
  }
  .card--front .wordmark {
    position: absolute;
    left: 0; right: 0; top: 0; bottom: 0;
    justify-content: center;
    font-size: 46px;
  }
  .card--back .wordmark {
    position: absolute;
    left: 44px;
    top: 168px;
    font-size: 32px;
    gap: 10px;
  }
  .card--back .wordmark__dot {
    width: 11px;
    height: 11px;
  }
  .divider {
    position: absolute;
    left: 340px;
    top: 70px;
    width: 2px;
    height: 260px;
    background: var(--ink-soft);
  }
  .contact {
    position: absolute;
    left: 372px;
    top: 76px;
    font-family: "Work Sans", sans-serif;
    color: var(--ink-soft);
  }
  .contact__name {
    margin: 0;
    font-size: 28px;
    font-weight: 500;
    letter-spacing: 0.5px;
    text-transform: uppercase;
    color: var(--ink-muted);
  }
  .contact__role {
    margin: 0 0 18px;
    font-size: 16px;
  }
  .contact__address {
    margin: 0 0 14px;
    font-size: 18px;
    line-height: 1.35;
    font-style: normal;
  }
  .contact__list {
    list-style: none;
    margin: 0;
    padding: 0;
    font-size: 18px;
    line-height: 1.35;
  }
  .contact__list li {
    display: flex;
    align-items: center;
    gap: 10px;
  }
  .contact__list svg {
    width: 13px;
    height: 13px;
    flex: none;
  }
</style>
</head>
<body>
<main class="sheet">
  <section class="card card--front" aria-label="Card front">
    <div class="wordmark"><span class="wordmark__dot"></span>Harlow Advisory</div>
  </section>

  <section class="card card--back" aria-label="Card back">
    <div class="wordmark"><span class="wordmark__dot"></span>Harlow Advisory</div>
    <div class="divider"></div>
    <div class="contact">
      <h1 class="contact__name">Daniel Hart</h1>
      <p class="contact__role">Director</p>
      <address class="contact__address">48 Harbour Ln,<br>Easton VIC 3712</address>
      <ul class="contact__list">
        <li>
          <svg viewBox="0 0 16 16" aria-hidden="true"><path d="M4 1.5l2.2 3-1.3 1.6c.9 2 2.6 3.6 4.5 4.5l1.6-1.3 3 2.2-1.2 2.4C7 13.5 2.5 9 2 3z" fill="none" stroke="#d6d6d6" stroke-width="1.3" stroke-linejoin="round"/></svg>
          +330 5812-4406
        </li>
        <li>
          <svg viewBox="0 0 16 16" aria-hidden="true"><rect x="1.5" y="3.5" width="13" height="9" fill="none" stroke="#d6d6d6" stroke-width="1.3"/><path d="M1.5 3.5L8 9l6.5-5.5" fill="none" stroke="#d6d6d6" stroke-width="1.3"/></svg>
          info@harlowadvisory.com
        </li>
        <li>
          <svg viewBox="0 0 16 16" aria-hidden="true"><circle cx="8" cy="8" r="6.5" fill="none" stroke="#d6d6d6" stroke-width="1.2"/><ellipse cx="8" cy="8" rx="3" ry="6.5" fill="none" stroke="#d6d6d6" stroke-width="1.2"/><path d="M1.5 8h13" stroke="#d6d6d6" stroke-width="1.2"/></svg>
          www.harlowadvisory.com
        </li>
      </ul>
    </div>
  </section>
</main>
</body>
</html>
```